New Business Card Design Project

I need a design for business cards, i am an electrical business called "Corvane Electrical and Communications" i need the cards to be double sided with the company logo on the back (attached) the front needs to say my company name, web site, email address, telephone number, and ABN number and electrical license number. I am open to different arrangements of the information but would like the background to be incorporating something electrical or something that looks smart. open to all additional ideas also.

The company colours are orange and grey see logo attached.

Business Name: Corvane Electrical and Communications
Website: corvaneelectricalandcomms.example.com.au
Email: brent@corvaneelectricalandcomms.example.com.au
Telephone(mobile): 0481209736
ABN: 71208349162
Lic No: 418273D

Target Market(s)

Business entities, Project Managers, Accounts, Clients

Industry/Entity Type

Electrician

Contact Information for Business Card

I need a design for business cards, i am an electrical business called "Corvane Electrical and Communications" i need the cards to be double sided with the company logo on the back (attached) the front needs to say my company name

Font styles to use
Serif
Sans Serif

Colors
f37122
5c5c5c

Requirements
Must have
• Must have the Logo on the back open to different ways of it being on the back but had in mind to keep it central but again open to other options
Nice to have
• A real modern cool background that is eye catching yet contemporary
Should not have
• No backgrounds of a light bulb or plug or anything like that

```html
<!DOCTYPE html>
<html lang="en">
<head>
<meta charset="UTF-8">
<title>Corvane Electrical and Communications – Business Card</title>
<link rel="stylesheet" href="https://fonts.googleapis.com/css2?family=Open+Sans:wght@300;400;600;700&display=swap">
<style>
  :root {
    --stage: #000000;
    --card: #59595b;
    --accent: #f2a71b;
    --text: #ffffff;
  }
  * { margin: 0; padding: 0; box-sizing: border-box; }
  html, body {
    width: 1200px;
    height: 900px;
    overflow: hidden;
    background: var(--stage);
    font-family: "Open Sans", Arial, sans-serif;
    color: var(--text);
  }
  .canvas { position: relative; width: 1200px; height: 900px; }

  .card {
    position: absolute;
    top: 275px;
    width: 477px;
    height: 294px;
    background: var(--card);
  }
  .card--front { left: 116px; border-radius: 0 56px 0 56px; }
  .card--back  { left: 622px; border-radius: 56px 0 56px 0; }

  /* wordmark */
  .wordmark { position: absolute; }
  .wordmark__name {
    display: block;
    font-weight: 300;
    color: var(--text);
    letter-spacing: 0.12em;
    line-height: 1;
  }
  .wordmark__tagline {
    display: block;
    font-weight: 600;
    color: var(--accent);
    letter-spacing: 0.08em;
    text-transform: uppercase;
    white-space: nowrap;
  }
  .card--front .wordmark { left: 38px; top: 78px; }
  .card--front .wordmark__name { font-size: 40px; }
  .card--front .wordmark__tagline { font-size: 9.6px; margin-top: 6px; }

  .card--back .wordmark { left: 0; right: 0; top: 138px; text-align: center; }
  .card--back .wordmark__name { font-size: 54px; }
  .card--back .wordmark__tagline { font-size: 13.5px; margin-top: 8px; }

  /* person */
  .person { position: absolute; right: 28px; top: 38px; text-align: right; }
  .person__name { font-size: 17px; font-weight: 700; color: var(--accent); line-height: 1.2; }
  .person__role { font-size: 13px; font-weight: 400; line-height: 1.3; }

  /* registration */
  .registration { position: absolute; right: 30px; top: 151px; text-align: right; }
  .registration__line { font-size: 14px; font-weight: 700; line-height: 20px; }
  .registration__value { font-size: 13px; font-weight: 600; }

  /* contact list */
  .contacts { position: absolute; right: 28px; top: 205px; list-style: none; text-align: right; }
  .contacts__item {
    display: flex;
    justify-content: flex-end;
    align-items: center;
    gap: 7px;
    font-size: 12.6px;
    line-height: 20px;
    white-space: nowrap;
  }
  .contacts__icon { width: 11px; height: 11px; flex: none; fill: var(--accent); }

  .website {
    position: absolute;
    left: 0; right: 0; top: 243px;
    text-align: center;
    font-size: 15px;
    font-weight: 700;
  }
</style>
</head>
<body>
<main class="canvas">

  <section class="card card--front" aria-label="Business card front">
    <div class="wordmark">
      <span class="wordmark__name">CORVANE</span>
      <span class="wordmark__tagline">Electrical &amp; Communications</span>
    </div>

    <div class="person">
      <p class="person__name">Dale Harper</p>
      <p class="person__role">Director</p>
    </div>

    <div class="registration">
      <p class="registration__line">ABN: <span class="registration__value">71208349162</span></p>
      <p class="registration__line">Lic No: <span class="registration__value">418273D</span></p>
    </div>

    <ul class="contacts">
      <li class="contacts__item">0481209736
        <svg class="contacts__icon" viewBox="0 0 24 24" aria-hidden="true"><path d="M6.6 10.8a15.1 15.1 0 0 0 6.6 6.6l2.2-2.2c.3-.3.7-.4 1-.2 1.1.4 2.3.6 3.6.6.6 0 1 .4 1 1V20c0 .6-.4 1-1 1C10.6 21 3 13.4 3 4c0-.6.4-1 1-1h3.5c.6 0 1 .4 1 1 0 1.3.2 2.5.6 3.6.1.3 0 .7-.2 1z"/></svg>
      </li>
      <li class="contacts__item">brent@corvaneelectricalandcomms.example.com.au
        <svg class="contacts__icon" viewBox="0 0 24 24" aria-hidden="true"><path d="M2 5h20v14H2z M3.5 6.5 12 13l8.5-6.5" fill="var(--accent)"/><path d="M3 6l9 7 9-7" fill="none" stroke="#59595b" stroke-width="1.8"/></svg>
      </li>
      <li class="contacts__item">corvaneelectricalandcomms.example.com.au
        <svg class="contacts__icon" viewBox="0 0 24 24" aria-hidden="true"><circle cx="12" cy="12" r="10"/><path d="M2 12h20M12 2c3 3 3 17 0 20M12 2c-3 3-3 17 0 20" fill="none" stroke="#59595b" stroke-width="1.5"/></svg>
      </li>
    </ul>
  </section>

  <section class="card card--back" aria-label="Business card back">
    <div class="wordmark">
      <span class="wordmark__name">CORVANE</span>
      <span class="wordmark__tagline">Electrical &amp; Communications</span>
    </div>
    <p class="website">corvaneelectricalandcomms.example.com.au</p>
  </section>

</main>
</body>
</html>
```